Wordpress website design for a high-end painting business

We are currently rebranding and are looking to update our Wordpress theme. We have recently rebranded our logo on PixelHarbor, and would like our website to be equally as refined.
Our business is named “Fenwick Painters”. We are a high-end painting business that is known for being professional and having high standards. Our clean and professional image is important as it separates us from our competition. Our current website can be found at www.fenwickcoatings.co.nz . We designed the site ourselves so it is understandably rudimentary. We are generally happy with the. page layout of our existing site, but we like a professional remodel. Any ideas on improvement welcomed.
We would like the front page of the website to summarise all of the info throughout the whole website (I.e introduction, photos, testimonials, contact info etc.) as visitors typically scroll through the first page to see that we are reputable and get to our contact number/email contact at the bottom of the page. We would like this first page to give a clean well rounded image of our business. We would like the gallery to be a scroll through of large photos, as it is difficult to see paint details in smaller photos. A contact page with an enquiry section would also be good.
For the colour scheme, we would like something that fits a bold, masculine and high end theme (similar to our logo attached).
We would like the footer to include Velmora paint logos and the accredited painter logo we have included as these are important to our profession.
We have attached some photos of our work also. I will add more in the coming days. More can also be found on our website.
If you have questions or comments, please don’t hesitate to ask and I will get back as soon as possible.
We are open to your own interpretation or ideas for a better layout/site provided they fit the general brief of being a well rounded site for our profession.
Thanks,
Fenwick Painters.
Target Market(s)
High end clients
Industry/Entity Type
Painting (interior and exterior)
Coding
Coded - Design and coding required
Requirements
Must have
- Classy feel, separating us from typical painting companies. Well rounded homepage.
Nice to have
- Lots of examples of our work
Should not have
- Untidy paint motifs (eg, paint droplets, paint splashes)

```html
<!DOCTYPE html>
<html lang="en">
<head>
<meta charset="utf-8">
<title>Fenwick Painters</title>
<link href="https://fonts.googleapis.com/css2?family=Libre+Baskerville:wght@400;700&family=Roboto:ital,wght@0,400;0,500;0,700;1,400&display=swap" rel="stylesheet">
<style>
:root{
  --navy:#1c2535;
  --navy-deep:#141b28;
  --bronze:#7a5c36;
  --bronze-dark:#5e4527;
  --ink:#1f1f1f;
  --white:#fff;
  --sky:#7fa3c8;
  --stucco:#cdbfa8;
  --lawn:#5a7a32;
  --room:#e4ddd2;
  --carpet:#2e3a58;
  --cladding:#9aa2ab;
}
*{box-sizing:border-box;margin:0;padding:0}
html,body{width:1200px;height:4112px;overflow:hidden}
body{position:relative;background:var(--white);font-family:"Roboto",Arial,sans-serif;color:var(--ink)}
.abs{position:absolute}

/* Hero */
.hero{left:0;top:0;width:1200px;height:686px;background:linear-gradient(180deg,var(--sky) 0%,#a9bccd 18%,var(--stucco) 30%,#b5a287 52%,#6f7a48 70%,var(--lawn) 100%)}
.nav{left:112px;top:64px;width:976px;height:88px;background:var(--white);border-radius:4px;box-shadow:0 2px 10px rgba(0,0,0,.15)}
.nav a{position:absolute;top:34px;font-size:15px;color:var(--ink);text-decoration:none}
.nav-logo{left:525px;top:36px;width:150px;height:166px;border-radius:75px;background:var(--white);display:flex;align-items:flex-end;justify-content:center;text-align:center;padding-bottom:26px}
.nav-logo .name{font-family:"Libre Baskerville",Georgia,serif;font-weight:700;font-size:17px;color:var(--navy);line-height:1.2}
.btn-contact{position:absolute;left:822px;top:22px;width:122px;height:44px;border-radius:22px;background:var(--bronze);color:var(--white);font-weight:700;font-size:15px;display:flex;align-items:center;justify-content:center}
.hero-arrow{top:318px}
.welcome{left:148px;top:231px;width:400px;height:400px;border-radius:50%;background:var(--white);text-align:center}
.welcome .pre{margin-top:84px;font-family:"Libre Baskerville",Georgia,serif;font-size:28px;color:var(--bronze)}
.welcome h1{font-family:"Libre Baskerville",Georgia,serif;font-weight:700;font-size:60px;line-height:1.18;color:var(--bronze);margin-top:14px}
.btn-outline{display:inline-flex;align-items:center;justify-content:center;border:2px solid var(--bronze-dark);border-radius:24px;color:var(--bronze-dark);font-weight:700;font-size:15px}
.welcome .btn-outline{margin-top:20px;width:138px;height:44px}

/* Sections */
.section-title{left:0;width:1200px;text-align:center;font-family:"Libre Baskerville",Georgia,serif;font-weight:700;font-size:32px;color:var(--bronze)}
.service{width:300px;text-align:center}
.service .photo{width:272px;height:272px;border-radius:50%;margin:0 auto;border:6px solid #fff;box-shadow:0 0 0 3px var(--navy)}
.service h3{font-family:"Libre Baskerville",Georgia,serif;font-weight:700;font-size:28px;color:var(--ink);margin-top:26px}

.about{left:0;top:1692px;width:1200px;height:602px;background:var(--navy)}
.about h2{position:absolute;left:115px;top:88px;font-family:"Libre Baskerville",Georgia,serif;font-weight:700;font-size:32px;color:var(--white)}
.about p{position:absolute;left:115px;top:140px;width:462px;font-size:14.6px;line-height:25.7px;color:#e9ecf1;text-align:justify}
.about .btn-light{position:absolute;left:115px;top:469px;width:136px;height:44px;border-radius:22px;background:var(--white);color:var(--bronze-dark);font-weight:700;font-size:15px;display:flex;align-items:center;justify-content:center}
.about .feature{position:absolute;left:700px;top:96px;width:420px;height:420px;border-radius:50%;background:linear-gradient(180deg,#dcd8cc 0%,#c7c0ae 55%,#56663f 100%)}

.card{top:2469px;width:474px;height:335px;background:var(--white);box-shadow:0 2px 12px rgba(0,0,0,.14)}
.avatar{position:absolute;width:116px;height:116px;border-radius:50%;background:linear-gradient(180deg,#d8d2c8,#a08a72);border:3px solid #fff;box-shadow:0 0 0 2px #888}
.card .who{position:absolute;text-align:center;font-family:"Libre Baskerville",Georgia,serif;font-size:16px;color:var(--ink);line-height:1.45}
.card .quote{position:absolute;font-style:italic;font-size:12.6px;line-height:25.6px;color:#333;text-align:justify}
.card .mark{position:absolute;font-family:"Libre Baskerville",Georgia,serif;font-size:64px;color:#cfcfcf;line-height:1}
.t-arrow{top:2621px;width:34px;height:32px;display:flex;align-items:center;justify-content:center;border-radius:3px}

.gallery{left:0;top:2892px;width:1200px;height:804px;background:linear-gradient(180deg,#252f3f,#1c2535)}
.gallery .section-title{color:var(--white);top:90px}
.tile{width:305px;height:229px;border:2px solid #fff}
.btn-view{left:532px;top:3589px;width:136px;height:46px;border-radius:23px;background:var(--white);color:var(--ink);font-weight:700;font-size:14px;display:flex;align-items:center;justify-content:center}

.footer{left:0;top:3696px;width:1200px;height:416px;background:var(--navy-deep)}
.footer .brand{position:absolute;left:116px;top:180px;font-family:"Libre Baskerville",Georgia,serif;font-weight:700;font-size:22px;color:var(--white);line-height:1.3;display:flex;align-items:center;gap:12px}
.footer .brand .dot{width:40px;height:40px;border-radius:50%;border:2px solid var(--white)}
.footer h4{position:absolute;top:106px;font-family:"Libre Baskerville",Georgia,serif;font-weight:400;font-size:20px;color:var(--white)}
.footer ul{position:absolute;list-style:none;font-size:14px;line-height:28.5px;color:#e6e9ee}
.contact-row{position:absolute;display:flex;gap:14px;font-size:14.5px;color:#e6e9ee;line-height:24px}
.social{position:absolute;left:116px;top:278px;display:flex;gap:18px;font-size:14px;color:var(--white);font-weight:500}
.copyright{position:absolute;left:112px;top:354px;font-size:14px;color:#e6e9ee}
.badge{position:absolute;left:932px;top:318px;width:121px;height:76px;background:#2a78c4;border-radius:2px}
</style>
</head>
<body>

<!-- Hero -->
<div class="abs hero" role="img" aria-label="Photograph of a large two-storey home with a freshly painted exterior, flower garden and lawn"></div>
<nav class="abs nav">
  <a style="left:32px">Home</a>
  <a style="left:116px">Services</a>
  <a style="left:216px">Gallery</a>
  <a style="left:306px">About</a>
  <a style="left:620px">Testimonials</a>
  <svg class="abs" style="left:754px;top:36px" width="18" height="18" viewBox="0 0 18 18" fill="none" stroke="#7a5c36" stroke-width="2.4"><circle cx="7.5" cy="7.5" r="5.5"/><line x1="11.5" y1="11.5" x2="16" y2="16"/></svg>
  <div class="btn-contact">CONTACT</div>
</nav>
<div class="abs nav-logo"><div class="name">FENWICK<br>PAINTERS</div></div>
<svg class="abs hero-arrow" style="left:60px" width="30" height="50" viewBox="0 0 30 50" fill="none" stroke="#fff" stroke-width="5"><polyline points="24,4 6,25 24,46"/></svg>
<svg class="abs hero-arrow" style="left:1108px" width="30" height="50" viewBox="0 0 30 50" fill="none" stroke="#fff" stroke-width="5"><polyline points="6,4 24,25 6,46"/></svg>
<div class="abs welcome">
  <div class="pre">WELCOME TO</div>
  <h1>FENWICK<br>PAINTERS</h1>
  <div class="btn-outline">GET STARTED</div>
</div>

<!-- Services -->
<h2 class="abs section-title" style="top:764px">OUR SERVICES</h2>
<div class="abs service" style="left:100px;top:885px"><div class="photo" role="img" aria-label="Photograph of a painted house exterior" style="background:linear-gradient(180deg,#a9c4de 0%,#d6d3cc 40%,#4d5147 62%,#6ea43c 80%)"></div><h3>Exterior Painting</h3></div>
<div class="abs service" style="left:448px;top:885px"><div class="photo" role="img" aria-label="Photograph of a freshly painted living room interior" style="background:linear-gradient(180deg,#ece6dc 0%,#ddd3c3 55%,#8c847c 75%)"></div><h3>Interior Painting</h3></div>
<div class="abs service" style="left:795px;top:885px"><div class="photo" role="img" aria-label="Photograph of a patterned wallpapered feature wall" style="background:#767a71"></div><h3>Wallpapering</h3></div>
<div class="abs service" style="left:100px;top:1268px"><div class="photo" role="img" aria-label="Photograph of plastering work on a wall" style="background:linear-gradient(135deg,#f1f1ee 0%,#f1f1ee 55%,#3a3a3a 55%,#2a2a2a 100%)"></div><h3>Plastering</h3></div>
<div class="abs service" style="left:448px;top:1268px"><div class="photo" role="img" aria-label="Photograph of a cleaned brick and weatherboard house" style="background:linear-gradient(180deg,#6d9dd6 0%,#dfe3e6 38%,#8a4a3a 62%,#5c8a34 82%)"></div><h3>House Cleaning</h3></div>
<div class="abs service" style="left:795px;top:1268px"><div class="photo" role="img" aria-label="Photograph of a painted roof and cladding" style="background:linear-gradient(180deg,#8ca7c9 0%,#4a5057 35%,#a9a4a8 55%,#a9a4a8 100%)"></div><h3>Roof Painting</h3></div>

<!-- About -->
<section class="abs about">
  <h2>ABOUT US</h2>
  <p>Here at Fenwick Painters, we take a lot of pride in our work. We strive to ensure the highest quality paint-work, paying close attention to detail to provide a long lasting finish. Our clients are always our priority, we aim to deliver beyond their expectations. It is our goal to provide an excellent service from start to finish through clear communication, free quoting and transparency with our pricing. We take great pride in the preparation of surfaces for painting and only use the best quality products to ensure we achieve the best finish for you. Our qualified interior designer can also assist you with your colour selection as a part of our free colour consultancy service. If you are looking at painting your property, or have any questions, please don't hesitate to call Rowan on 021 5550148.</p>
  <div class="btn-light">LEARN MORE</div>
  <div class="feature" role="img" aria-label="Photograph of a painted two-storey house exterior"></div>
</section>

<!-- Testimonials -->
<h2 class="abs section-title" style="top:2374px">OUR TESTIMONIALS</h2>
<div class="abs t-arrow" style="left:63px;background:var(--bronze)"><svg width="16" height="12" viewBox="0 0 16 12" fill="none" stroke="#fff" stroke-width="2"><line x1="15" y1="6" x2="2" y2="6"/><polyline points="6,1 1,6 6,11"/></svg></div>
<div class="abs t-arrow" style="left:1096px;border:2px solid var(--bronze)"><svg width="16" height="12" viewBox="0 0 16 12" fill="none" stroke="#7a5c36" stroke-width="2"><line x1="1" y1="6" x2="14" y2="6"/><polyline points="10,1 15,6 10,11"/></svg></div>

<div class="abs card" style="left:112px">
  <div class="avatar" style="left:37px;top:90px" role="img" aria-label="Portrait photo of the reviewer"></div>
  <div class="who" style="left:10px;top:236px;width:170px">MARCUS DALE</div>
  <div class="mark" style="left:148px;top:30px">&ldquo;</div>
  <div class="quote" style="left:196px;top:34px;width:244px">Just had our house interior painted throughout by Fenwicks. They were professional right from the start. They turned up to give a quote when other firms never responded. They were spot on with their time and cost estimates and never missed a day ..we had to ask them not to work on Public Holidays. They have an attention to detail and a level of care that is above what I've seen previously.</div>
</div>
<div class="abs card" style="left:606px">
  <div class="avatar" style="left:37px;top:90px" role="img" aria-label="Portrait photo of the reviewer"></div>
  <div class="who" style="left:10px;top:236px;width:170px">PETRA<br>HALVORSEN</div>
  <div class="mark" style="left:158px;top:48px">&ldquo;</div>
  <div class="quote" style="left:197px;top:52px;width:242px">Rowan and his Team have done an amazing job painting our house. Without a doubt hiring them was our best decision. Attention to detail, great communication, respect towards our needs, working within the budget are just a few things to describe them. I will be recommending Fenwick Painters and Decorators for many years to come. Thank you, Guys!</div>
</div>

<!-- Gallery -->
<section class="abs gallery">
  <h2 class="section-title abs">OUR GALLERY</h2>
</section>
<div class="abs tile" style="left:112px;top:3056px;background:linear-gradient(180deg,#a7bccf 0%,#c4cbd2 55%,#6f8e55 80%)" role="img" aria-label="Photograph of a repainted grey weatherboard cottage"></div>
<div class="abs tile" style="left:448px;top:3056px;background:linear-gradient(180deg,#c9d6e2 0%,#8f9aa4 45%,#2f3338 70%,#5b7a3f 88%)" role="img" aria-label="Photograph of a two-storey house painted grey with dark base"></div>
<div class="abs tile" style="left:785px;top:3056px;background:linear-gradient(180deg,#efece6 0%,#e2ddd5 60%,#2c3a5c 80%)" role="img" aria-label="Photograph of a freshly painted lounge interior"></div>
<div class="abs tile" style="left:112px;top:3328px;background:linear-gradient(180deg,#efece6 0%,#e2ddd5 60%,#2c3a5c 80%)" role="img" aria-label="Photograph of a painted lounge with fireplace"></div>
<div class="abs tile" style="left:448px;top:3328px;background:linear-gradient(180deg,#3f7fd4 0%,#dfe4ea 40%,#5a6478 62%,#7a4a2a 80%,#5e8a3a 92%)" role="img" aria-label="Photograph of a white and grey painted house under blue sky"></div>
<div class="abs tile" style="left:785px;top:3328px;background:linear-gradient(180deg,#3f7fd4 0%,#f2f2f0 40%,#e6e6e2 68%,#8a4a2a 82%,#5e8a3a 92%)" role="img" aria-label="Photograph of a white painted bungalow"></div>
<div class="abs btn-view">VIEW ALL</div>

<!-- Footer -->
<footer class="abs footer">
  <div class="brand"><span class="dot"></span><span>FENWICK<br>PAINTERS</span></div>
  <div class="social"><span>Kitelink</span><span>Chirpa</span><span>Lensly</span><span>Workweb</span></div>

  <h4 style="left:428px">QUICK LINKS</h4>
  <ul style="left:428px;top:152px"><li>Home</li><li>Services</li><li>Gallery</li><li>About</li><li>Contact</li><li>Testimonials</li></ul>

  <h4 style="left:661px">CONTACT US</h4>
  <div class="contact-row" style="left:661px;top:148px"><svg width="14" height="24" viewBox="0 0 14 24"><path d="M3 6c1-1 2-1 3 0l1 2c.4 1-.3 1.5-1 2 .6 1.6 1.6 2.8 3 3.6.6-.6 1.2-1.2 2-.8l2 1c1 .6 1 1.6 0 2.6-2 2-6 0-8.4-3C2 10 1.6 8 3 6z" fill="#fff"/></svg><span>021 555 0148</span></div>
  <div class="contact-row" style="left:661px;top:192px"><svg width="14" height="24" viewBox="0 0 14 24" fill="none" stroke="#fff" stroke-width="1.6"><rect x="1" y="7" width="12" height="9"/><polyline points="1,7 7,12 13,7"/></svg><span>hello@fenwickpainters.example</span></div>
  <div class="contact-row" style="left:661px;top:236px"><svg width="14" height="24" viewBox="0 0 14 24"><path d="M7 4a5 5 0 0 1 5 5c0 4-5 9-5 9S2 13 2 9a5 5 0 0 1 5-5z" fill="#fff"/><circle cx="7" cy="9" r="1.8" fill="#141b28"/></svg><span>Rowan<br>Tallis</span></div>

  <h4 style="left:959px">COMPANY</h4>
  <ul style="left:959px;top:152px"><li>Terms&amp;condtions</li><li>Privacy Policy</li><li>About Us</li><li>Support</li></ul>

  <div class="copyright">&copy;Copyrights 2022 Fenwickdecorators &nbsp;| &nbsp;&nbsp;All Rights Reserved</div>
  <div class="badge" role="img" aria-label="Velmora accredited painter badge"></div>
</footer>

</body>
</html>
```